Dietitian needs awesome business card

I need a contemporary design that's eye catching but professional.
My card is to given to doctors, specialists and patients alike.
I manage patients with chronic diseases
I have uploaded my logo and current business card, I would also like the other Certified Clinical Nutritionist logo incorporated into the design

Target Market(s)

Doctors, specialists and patients

Industry/Entity Type

Healthcare

Contact Information for Business Card

www.brightfieldnutrition.com.au
Ph: 0427 561 903
Fax: 6457 2183
email: marcus.k.diet@fernmail.com
Space on the back of the card with: Appointment date, Appointment time and appointment location

Font styles to use
Serif

Colors
fbee3e
876aae
ffc214

Requirements
Must have
• My Logo
• Certified Clinical Nutritionist Logo
• My 4 locations - Pinebrook Medical Centre, North Corrin Health, Hollis Medical, Ashcombe Doctors Surgery
Nice to have
• I like the colours in my current business card

```html
<!DOCTYPE html>
<html lang="en">
<head>
<meta charset="utf-8">
<title>Brightfield Nutrition &amp; Dietetics – Business Card</title>
<link href="https://fonts.googleapis.com/css2?family=Libre+Franklin:wght@400;500;600&display=swap" rel="stylesheet">
<style>
  :root {
    --backdrop: #2e2e30;
    --card: #ffffff;
    --navy: #1d2a8a;
    --orange: #f0781e;
    --green: #7cbf1e;
    --ink: #4a4a4a;
    --rule: #c8c8c8;
    --produce-light: #f4f6f1;
    --produce-mid: #e3ead9;
  }
  * { margin: 0; padding: 0; box-sizing: border-box; }
  html, body { width: 1200px; height: 987px; overflow: hidden; }
  body {
    background: var(--backdrop);
    font-family: "Libre Franklin", Arial, sans-serif;
    position: relative;
  }
  .card {
    position: absolute;
    left: 293px;
    width: 615px;
    height: 352px;
    background: var(--card);
    border-radius: 21px;
    overflow: hidden;
    box-shadow: 0 3px 10px rgba(0,0,0,.45);
  }
  .card--front { top: 128px; }
  .card--back { top: 507px; }

  .produce-photo { position: absolute; }
  .card--front .produce-photo {
    right: 0; top: 0; width: 340px; height: 352px;
    background: radial-gradient(ellipse at 75% 30%, var(--produce-mid) 0%, var(--produce-light) 45%, rgba(255,255,255,0) 75%);
  }
  .card--back .produce-photo {
    inset: 0;
    background: linear-gradient(100deg, var(--produce-mid) 0%, var(--produce-light) 40%, #f7f8f5 70%, var(--produce-mid) 100%);
    opacity: .8;
  }

  .brand { position: absolute; left: 32px; top: 48px; display: flex; align-items: center; gap: 14px; }
  .brand__dot { width: 60px; height: 60px; border-radius: 50%; background: var(--navy); }
  .brand__name { color: var(--navy); font-size: 24px; font-weight: 500; line-height: 1.15; }

  .person { position: absolute; right: 34px; top: 182px; text-align: right; }
  .person__name { color: var(--navy); font-size: 22px; font-weight: 600; line-height: 28px; }
  .person__role { font-size: 16.5px; line-height: 24px; }
  .person__role--orange { color: var(--orange); }
  .person__role--green { color: var(--green); }

  .divider { position: absolute; left: 33px; right: 34px; top: 268px; height: 1px; background: #8a8a8a; }

  .contact { position: absolute; top: 279px; font-size: 16px; color: var(--ink); line-height: 24px; }
  .contact--left { left: 33px; }
  .contact--right { right: 34px; text-align: right; }
  .contact__row { display: flex; align-items: center; gap: 9px; }
  .contact--right .contact__row { justify-content: flex-end; }
  .contact__icon { width: 16px; height: 16px; fill: var(--navy); flex: none; }

  .appointment__title {
    position: absolute; top: 30px; left: 0; right: 0; text-align: center;
    color: var(--navy); font-size: 20px; font-weight: 600;
  }
  .appointment__line { position: absolute; left: 42px; width: 530px; height: 1px; background: var(--rule); }
  .appointment__when {
    position: absolute; left: 42px; top: 222px; width: 530px;
    color: var(--navy); font-size: 16.5px; display: flex; align-items: baseline; white-space: nowrap;
  }
  .dots { color: var(--navy); letter-spacing: 1px; overflow: hidden; font-size: 13px; }
  .ampm { font-size: 12.5px; margin-left: 6px; }
  .locations {
    position: absolute; left: 42px; top: 263px; width: 540px;
    display: grid; grid-template-columns: 306px 1fr; row-gap: 4px;
    font-size: 16px; color: var(--ink); list-style: none;
  }
  .locations li { display: flex; align-items: center; gap: 6px; line-height: 20px; }
  .checkbox { width: 13px; height: 13px; border: 1.5px solid var(--navy); flex: none; }
</style>
</head>
<body>
  <section class="card card--front">
    <div class="produce-photo" role="img" aria-label="Faint photograph of fresh green vegetables"></div>
    <div class="brand">
      <span class="brand__dot"></span>
      <span class="brand__name">Brightfield<br>Nutrition &amp; Dietetics</span>
    </div>
    <div class="person">
      <p class="person__name">Marcus Kendrick</p>
      <p class="person__role person__role--orange">Certified Clinical Nutritionist</p>
      <p class="person__role person__role--green">Nutritionist &amp; Chef</p>
    </div>
    <div class="divider"></div>
    <div class="contact contact--left">
      <p class="contact__row">
        <svg class="contact__icon" viewBox="0 0 16 16"><path d="M3.6 1.2l2.3 2.8-1.3 1.7c.9 2 2.4 3.5 4.4 4.5l1.7-1.3 2.8 2.3-1.3 2.5C7.6 15 1 8.4 1.2 2.5z"/></svg>
        0427 561 903
      </p>
      <p class="contact__row">
        <svg class="contact__icon" viewBox="0 0 16 16"><rect x="4" y="1" width="8" height="5"/><rect x="1" y="6" width="14" height="8" rx="1.5"/><rect x="4" y="10" width="8" height="2" fill="#fff"/></svg>
        6457 2183
      </p>
    </div>
    <div class="contact contact--right">
      <p class="contact__row">
        marcus.k.diet@fernmail.com
        <svg class="contact__icon" viewBox="0 0 16 16"><rect x="1" y="3" width="14" height="10" rx="1"/><path d="M1.5 4l6.5 5 6.5-5" fill="none" stroke="#fff" stroke-width="1.4"/></svg>
      </p>
      <p class="contact__row">
        brightfieldnutrition.com.au
        <svg class="contact__icon" viewBox="0 0 16 16"><circle cx="8" cy="8" r="7"/><path d="M1 8h14M8 1c-3 3.5-3 10.5 0 14M8 1c3 3.5 3 10.5 0 14" fill="none" stroke="#fff" stroke-width="1"/></svg>
      </p>
    </div>
  </section>

  <section class="card card--back">
    <div class="produce-photo" role="img" aria-label="Faint photograph of celery and leafy vegetables"></div>
    <h2 class="appointment__title">YOUR APPOINTMENT</h2>
    <div class="appointment__line" style="top:83px"></div>
    <div class="appointment__line" style="top:118px"></div>
    <div class="appointment__line" style="top:154px"></div>
    <div class="appointment__line" style="top:189px"></div>
    <div class="appointment__when">
      <span>Date :&nbsp;&nbsp;</span>
      <span class="dots" style="width:218px">........................................................</span>
      <span>&nbsp;Time :&nbsp;</span>
      <span class="dots" style="width:142px">........................................</span>
      <span class="ampm">AM/PM</span>
    </div>
    <ul class="locations">
      <li><span class="checkbox"></span>Pinebrook Medical Centre</li>
      <li><span class="checkbox"></span>Hollis Medical</li>
      <li><span class="checkbox"></span>North Corrin Health</li>
      <li><span class="checkbox"></span>Ashcombe Doctors Surgery</li>
    </ul>
  </section>
</body>
</html>
```